Business Card Design for Online Gift Business

Business card design for a new online Canadian company called "Harlow & Brine Gift Boxes" selling modern and luxurious gift boxes for every occasion. Items are sourced locally from talented socially-responsible Canadian artisans. Each gift is elegantly presented in a keepsake wood box to ensure a lasting impression.

Industry/Entity Type

E-Commerce

Contact Information for Business Card

Marla Whitcombe, Proprietor
Calgary, AB
403-555-2741
www.harlowandbrine.ca
hello@harlowandbrine.ca

Requirements
Must have
• Gifts from our best, to your best
• Please also include the symbols for Facebook and Instagram
Nice to have
• **I have attached a few samples of background colors and font colors that I like. I hope this helps in a few directions to try.

```html
<!DOCTYPE html>
<html lang="en">
<head>
<meta charset="utf-8">
<title>Harlow &amp; Brine Gift Boxes — Business Card</title>
<link rel="stylesheet" href="https://fonts.googleapis.com/css2?family=Lato:wght@400;700&display=swap">
<style>
  :root {
    --stage: #070707;
    --paper: #ffffff;
    --tan: #b5a17a;
    --tan-deep: #a8936b;
    --ink: #1a1a1a;
    --white: #ffffff;
  }
  * { margin: 0; padding: 0; box-sizing: border-box; }
  html, body {
    width: 1200px; height: 900px; overflow: hidden;
    background: var(--stage);
    font-family: "Lato", sans-serif;
  }
  .stage { position: relative; width: 1200px; height: 900px; }
  .card {
    position: absolute; top: 170px;
    width: 347px; height: 561px; overflow: hidden;
  }
  .card-front { left: 259px; background: var(--paper); }
  .card-back { left: 631px; background: var(--tan); }

  .accent-band {
    position: absolute; left: 102px;
    width: 143px; height: 30px; background: var(--tan);
  }
  .accent-band.top { top: 0; }
  .accent-band.bottom { bottom: 0; height: 28px; }

  .brand-name {
    position: absolute; left: 0; right: 0;
    text-align: center;
    font-family: "Lato", sans-serif;
    font-weight: 400;
    letter-spacing: 1px;
    line-height: 1.1;
  }
  .card-front .brand-name { top: 170px; font-size: 40px; color: var(--tan); }
  .card-front .brand-tag {
    position: absolute; left: 0; right: 0; top: 222px;
    text-align: center; font-size: 15px; letter-spacing: 7px;
    color: var(--tan); text-transform: uppercase;
  }

  .contact {
    position: absolute; left: 0; right: 0; top: 369px;
    text-align: center; color: var(--ink);
  }
  .contact-name {
    font-size: 17px; font-weight: 700; color: var(--tan);
    text-transform: uppercase; letter-spacing: 0.3px;
  }
  .contact-role { font-size: 14px; margin-top: 1px; }
  .contact-city { font-size: 14px; margin-top: 15px; }
  .contact-line {
    display: flex; align-items: center; justify-content: center; gap: 4px;
    font-size: 14px;
  }
  .contact-line.phone { margin-top: 16px; }
  .contact-line.web { margin-top: 3px; }
  .contact-line svg { width: 11px; height: 11px; fill: var(--tan); }

  .back-watermark {
    position: absolute; left: -30px; top: 215px;
    font-size: 150px; line-height: 1; white-space: nowrap;
    color: var(--tan-deep); opacity: 0.6;
  }
  .card-back .brand-name { top: 248px; font-size: 42px; color: var(--white); }
  .card-back .brand-tag {
    position: absolute; left: 0; right: 0; top: 304px;
    text-align: center; font-size: 15px; letter-spacing: 7px;
    color: var(--white); text-transform: uppercase;
  }
</style>
</head>
<body>
<main class="stage">
  <section class="card card-front" aria-label="Business card front">
    <div class="accent-band top"></div>
    <p class="brand-name">Harlow &amp; Brine</p>
    <p class="brand-tag">Gift Boxes</p>
    <div class="contact">
      <p class="contact-name">Marla Whitcombe</p>
      <p class="contact-role">Proprietor</p>
      <p class="contact-city">Calgary, AB</p>
      <p class="contact-line phone">
        <svg viewBox="0 0 24 24" aria-hidden="true"><path d="M6.6 10.8a15 15 0 0 0 6.6 6.6l2.2-2.2c.3-.3.7-.4 1-.2 1.1.4 2.3.6 3.6.6.6 0 1 .4 1 1V20c0 .6-.4 1-1 1A17 17 0 0 1 3 4c0-.6.4-1 1-1h3.5c.6 0 1 .4 1 1 0 1.3.2 2.5.6 3.6.1.3 0 .7-.2 1z"/></svg>
        403-555-2741
      </p>
      <p class="contact-line web">
        <svg viewBox="0 0 24 24" aria-hidden="true"><path d="M12 2a10 10 0 1 0 0 20 10 10 0 0 0 0-20zm-1 17.9A8 8 0 0 1 4.1 10L9 15v1a2 2 0 0 0 2 2zm6.9-2.5A2 2 0 0 0 16 16h-1v-3a1 1 0 0 0-1-1H8v-2h2a1 1 0 0 0 1-1V7h2a2 2 0 0 0 2-2v-.4a8 8 0 0 1 2.9 12.8z"/></svg>
        www.harlowandbrine.ca
      </p>
    </div>
    <div class="accent-band bottom"></div>
  </section>

  <section class="card card-back" aria-label="Business card back">
    <p class="back-watermark" aria-hidden="true">Harlow &amp;</p>
    <p class="brand-name">Harlow &amp; Brine</p>
    <p class="brand-tag">Gift Boxes</p>
  </section>
</main>
</body>
</html>
```